Kinesiology undergraduate program needs an infographic

We would like an infographic to creatively and succinctly inform students, faculty, staff, and others about our undergraduate values and competencies (perhaps also integrating our mission and vision). We would like to see a design that incorporates the definition of Kinesiology (the study of human movement) and the colors of our Westbrook State University at Harlan.

```html
<!DOCTYPE html>
<html lang="en">
<head>
<meta charset="utf-8">
<title>Westbrook State University at Harlan – Kinesiology Mission, Values and Vision</title>
<link rel="stylesheet" href="https://fonts.googleapis.com/css2?family=Montserrat:wght@400;700;900&display=swap">
<style>
  :root {
    --brand-red: #d4112e;
    --navy: #1c1c44;
    --ink: #2b2b2b;
    --rule-grey: #c4c4c4;
    --margin-pink: #f2a3a8;
    --halo-grey: #e6e6e6;
    --figure-warm: #d98a6a;
    --figure-cool: #c9343a;
    --paper: #ffffff;
  }
  * { margin: 0; padding: 0; box-sizing: border-box; }
  html, body { width: 1200px; height: 848px; overflow: hidden; background: var(--paper); }
  .canvas {
    position: relative; width: 1200px; height: 848px; overflow: hidden;
    background: var(--paper);
    font-family: "Montserrat", Arial, sans-serif; color: var(--ink);
  }
  .notebook-rules { position: absolute; inset: 0; }
  .margin-line { position: absolute; top: 0; bottom: 0; width: 1px; background: var(--margin-pink); }
  .margin-line.first { left: 167px; }
  .margin-line.second { left: 176px; }

  .brand {
    position: absolute; left: 36px; top: 34px;
    font-weight: 700; font-size: 22px; line-height: 26px; color: var(--brand-red);
  }

  .headline {
    position: absolute; text-align: center; font-weight: 900; color: var(--brand-red);
    font-size: 44px; line-height: 52px; letter-spacing: 0.5px;
  }
  .headline.mission { left: 450px; width: 300px; top: 30px; }
  .headline.values { left: 110px; width: 250px; top: 146px; }
  .headline.vision { left: 840px; width: 250px; top: 157px; }

  .statement {
    position: absolute; text-align: center; font-weight: 400; font-size: 16px; line-height: 20.5px;
    white-space: nowrap;
  }
  .statement.mission { left: 400px; width: 400px; top: 127px; }
  .statement.values { left: 110px; width: 250px; top: 242px; }
  .statement.vision { left: 815px; width: 300px; top: 257px; }

  .pointer-triangle { position: absolute; left: 217px; top: 340px; }

  .figure-halo { position: absolute; left: 396px; top: 290px; width: 410px; height: 410px; border-radius: 50%; background: var(--halo-grey); }
  .figure-ground { position: absolute; left: 455px; top: 760px; width: 210px; height: 60px; border-radius: 50%; background: var(--halo-grey); }
  .figure-art {
    position: absolute; left: 495px; top: 226px; width: 250px; height: 582px; border-radius: 110px 110px 30px 30px;
    background: linear-gradient(to right, var(--figure-cool) 0%, var(--figure-cool) 42%, var(--figure-warm) 58%, var(--figure-warm) 100%);
    opacity: 0.85;
  }
  .divider { position: absolute; left: 598px; top: 220px; width: 5px; height: 608px; background: var(--navy); }

  .connectors { position: absolute; inset: 0; }

  .competency { position: absolute; font-size: 16px; line-height: 20.5px; font-weight: 400; white-space: nowrap; }
  .competency h2 { font-size: 16px; line-height: 20px; font-weight: 700; color: var(--navy); text-transform: uppercase; }
  .competency ul { list-style: none; }
  .competency.intrapersonal { left: 124px; top: 492px; }
  .competency.science { left: 124px; top: 652px; }
  .competency.reasoning { left: 860px; top: 492px; }
  .competency.relationships { left: 860px; top: 652px; }

  .icon { position: absolute; }
</style>
</head>
<body>
<main class="canvas">
  <svg class="notebook-rules" width="1200" height="848" viewBox="0 0 1200 848" stroke="var(--rule-grey)" stroke-width="2.5">
    <line x1="0" y1="101" x2="1200" y2="101"/>
    <line x1="0" y1="153" x2="1200" y2="153"/>
    <line x1="0" y1="205" x2="1200" y2="205"/>
    <line x1="0" y1="257" x2="1200" y2="257"/>
    <line x1="0" y1="309" x2="1200" y2="309"/>
    <line x1="0" y1="361" x2="1200" y2="361"/>
    <line x1="0" y1="413" x2="1200" y2="413"/>
    <line x1="0" y1="465" x2="1200" y2="465"/>
    <line x1="0" y1="517" x2="1200" y2="517"/>
    <line x1="0" y1="568" x2="1200" y2="568"/>
    <line x1="0" y1="620" x2="1200" y2="620"/>
    <line x1="0" y1="672" x2="1200" y2="672"/>
    <line x1="0" y1="723" x2="1200" y2="723"/>
    <line x1="0" y1="775" x2="1200" y2="775"/>
    <line x1="0" y1="827" x2="1200" y2="827"/>
  </svg>
  <div class="margin-line first"></div>
  <div class="margin-line second"></div>

  <div class="brand">WSUH<br>Kinesiology</div>

  <h1 class="headline mission">OUR<br>MISSION</h1>
  <p class="statement mission">To empower undergraduate students<br>to pursue excellence through<br>scientific discovery, clinical practice,<br>and health promotion</p>

  <h1 class="headline values">OUR<br>VALUES</h1>
  <p class="statement values">Student Success, Science,<br>and Service<br>Our Graduates Will Be<br>Competent In...</p>
  <svg class="pointer-triangle" width="18" height="16" viewBox="0 0 18 16"><polygon points="0,0 18,0 9,16" fill="var(--navy)"/></svg>

  <h1 class="headline vision">OUR<br>VISION</h1>
  <p class="statement vision">WSUH Kinesiology graduates are<br>leaders who excel in careers that<br>enhance the quality of life of<br>individuals and communities</p>

  <div class="figure-halo"></div>
  <div class="figure-ground"></div>
  <div class="figure-art" role="img" aria-label="Full-length figure of a student in a red hoodie, split down the middle to reveal the human muscular anatomy on the other half"></div>
  <div class="divider"></div>

  <svg class="connectors" width="1200" height="848" viewBox="0 0 1200 848" fill="none" stroke="var(--ink)" stroke-width="1.5">
    <polyline points="355,398 195,398 195,467"/>
    <circle cx="355" cy="398" r="5" fill="var(--ink)"/><circle cx="195" cy="467" r="5" fill="var(--ink)"/>
    <polyline points="413,611 387,611 387,665 310,665"/>
    <circle cx="413" cy="611" r="5" fill="var(--ink)"/><circle cx="310" cy="665" r="5" fill="var(--ink)"/>
    <polyline points="785,385 805,385 805,496 828,496"/>
    <circle cx="785" cy="385" r="5" fill="var(--ink)"/><circle cx="828" cy="496" r="5" fill="var(--ink)"/>
    <polyline points="746,572 800,572 800,664 835,664"/>
    <circle cx="746" cy="572" r="5" fill="var(--ink)"/><circle cx="835" cy="664" r="5" fill="var(--ink)"/>
  </svg>

  <svg class="icon pencil" style="left:110px;top:418px" width="60" height="58" viewBox="0 0 60 58" fill="none" stroke="var(--navy)" stroke-width="4" stroke-linejoin="round">
    <polygon points="14,4 56,46 54,54 46,54 4,14"/>
    <line x1="10" y1="20" x2="20" y2="10"/>
  </svg>
  <svg class="icon atom" style="left:42px;top:628px" width="70" height="70" viewBox="0 0 70 70" fill="none" stroke="var(--navy)" stroke-width="3.5">
    <ellipse cx="35" cy="35" rx="32" ry="12"/>
    <ellipse cx="35" cy="35" rx="32" ry="12" transform="rotate(60 35 35)"/>
    <ellipse cx="35" cy="35" rx="32" ry="12" transform="rotate(-60 35 35)"/>
    <circle cx="35" cy="35" r="5" fill="var(--navy)"/>
  </svg>
  <svg class="icon bulb" style="left:1090px;top:438px" width="80" height="80" viewBox="0 0 80 80" fill="none" stroke="var(--navy)" stroke-width="3.5" stroke-linecap="round">
    <path d="M30 56 C30 46 22 42 22 32 A18 18 0 0 1 58 32 C58 42 50 46 50 56 Z"/>
    <line x1="31" y1="63" x2="49" y2="63"/><line x1="33" y1="70" x2="47" y2="70"/>
    <line x1="40" y1="4" x2="40" y2="9"/><line x1="12" y1="32" x2="4" y2="32"/><line x1="68" y1="32" x2="76" y2="32"/>
    <line x1="16" y1="14" x2="11" y2="9"/><line x1="64" y1="14" x2="69" y2="9"/>
    <line x1="16" y1="50" x2="10" y2="55"/><line x1="64" y1="50" x2="70" y2="55"/>
  </svg>
  <svg class="icon target" style="left:1055px;top:622px" width="80" height="80" viewBox="0 0 80 80" fill="none" stroke="var(--navy)" stroke-width="3.5">
    <circle cx="40" cy="40" r="36"/><circle cx="40" cy="40" r="26"/>
    <polygon points="40,24 45,34 56,35 48,43 50,54 40,48 30,54 32,43 24,35 35,34"/>
  </svg>

  <section class="competency intrapersonal">
    <h2>Intrapersonal Growth</h2>
    <ul><li>Cultural Humility/Sensitivity</li><li>Integrity</li><li>Self-Directed</li><li>Dependability</li><li>Mission Oriented</li></ul>
  </section>
  <section class="competency science">
    <h2>The Science of<br>Kinesiology</h2>
    <ul><li>Foundational Concepts of<br>Kinesiology</li><li>Clinical Application</li><li>Scientific Communication</li></ul>
  </section>
  <section class="competency reasoning">
    <h2>Thinking and Reasoning</h2>
    <ul><li>Critical Thinking</li><li>Quantitative Reasoning</li><li>Scientific Inquiry</li><li>Concept Integration</li></ul>
  </section>
  <section class="competency relationships">
    <h2>Relationships and<br>Communication</h2>
    <ul><li>Cultural Competence</li><li>Professionalism</li><li>Leadership and Teamwork</li><li>Service</li><li>Orientation/Citizenship</li></ul>
  </section>
</main>
</body>
</html>
```